4th Generation Family Business Needs a New Card Design!

We are a family owned 4th Generation company. We are based in the Sydney, Australia area and we are desperately in need of a more modern and classy card. We are monumental masons who design, supply & erect lasting memorials throughout cemeteries in Sydney. Our customers are normally in a period of grieving. I have attached logo files that will need to be implemented on the card. Company was established 1935. Australian Owned and Operated. Card needs to be designed to PIXO.com specification.

Target Market(s)

Our target market is based upon people that a grieving for family members that have passed away. We also deal with alot of companies that own and operate cemeteries.

Industry/Entity Type

Business

Contact Information for Business Card

Simon Harcourt, Operations Manager, 0417293086, simon@harcourtmemorials.com.au
Lewis Harcourt, Director, 0491630572, lewis@harcourtmemorials.com.au
Phone # 02 9561 3048
Website: www.harcourtmemorials.com.au
Address: Suite 17, 8 Palfrey Lane, West Carlow, Sydney NSW 2156

Font styles to use
Serif
Decorative
Script

Requirements
Must have
• Would like to see the logo nicely implemented with a modern design. Embossed lettering would be a nice additive.

```html
<!DOCTYPE html>
<html lang="en">
<head>
<meta charset="UTF-8">
<title>Harcourt Memorials – Business Card</title>
<link href="https://fonts.googleapis.com/css2?family=Source+Sans+3:wght@400;600;700&display=swap" rel="stylesheet">
<style>
  :root {
    --backdrop: #000000;
    --card: #333438;
    --gold: #f2c230;
    --ink: #f1f1f1;
  }
  * { margin: 0; padding: 0; box-sizing: border-box; }
  html, body { width: 1200px; height: 900px; overflow: hidden; background: var(--backdrop); }
  body { position: relative; font-family: "Source Sans 3", "Helvetica Neue", Arial, sans-serif; color: var(--ink); }

  .card {
    position: absolute; top: 271px; width: 457px; height: 282px;
    background: var(--card); border-radius: 14px; overflow: hidden;
  }
  .card--front { left: 137px; }
  .card--back { left: 626px; }

  .brand-name {
    position: absolute; text-align: center; color: var(--ink);
    font-weight: 600; text-transform: uppercase; line-height: 1.1;
  }
  .card--front .brand-name { left: 248px; top: 92px; width: 186px; font-size: 24px; letter-spacing: 1px; }
  .card--back .brand-name { left: 100px; top: 112px; width: 257px; font-size: 32px; letter-spacing: 1.5px; }

  .person { position: absolute; font-size: 12.5px; line-height: 17px; }
  .person__name { color: var(--gold); font-weight: 700; font-size: 15px; line-height: 19px; }
  .person__role { font-size: 13px; margin-bottom: 3px; }
  .person--primary { left: 19px; top: 78px; }
  .person--secondary { right: 26px; top: 184px; text-align: right; }

  .contact-line { display: flex; align-items: center; gap: 6px; }
  .person--secondary .contact-line { justify-content: flex-end; }
  .icon { width: 9px; height: 9px; fill: var(--gold); flex: none; }

  .divider { position: absolute; left: 0; right: 0; top: 167px; height: 1.5px; background: var(--gold); }

  .company { position: absolute; left: 23px; top: 185px; font-size: 12.5px; line-height: 17.5px; }
  .company__label { color: var(--gold); font-weight: 600; }
</style>
</head>
<body>

<section class="card card--front">
  <div class="brand-name">Harcourt Memorials</div>

  <div class="person person--primary">
    <div class="person__name">Simon Harcourt</div>
    <div class="person__role">Operations Manager</div>
    <div class="contact-line">
      <svg class="icon" viewBox="0 0 10 10"><path d="M2 0.5 L3.6 2.6 L2.8 3.6 Q4 6 6.4 7.2 L7.4 6.4 L9.5 8 L8.3 9.5 Q2 8.5 0.5 1.7 Z"/></svg>
      <span>0417293086</span>
    </div>
    <div class="contact-line">
      <svg class="icon" viewBox="0 0 10 10"><path d="M0.5 2 H9.5 V8 H0.5 Z M1 2.5 L5 5.5 L9 2.5" stroke="#333438" stroke-width="0.8"/></svg>
      <span>simon@harcourtmemorials.com.au</span>
    </div>
  </div>

  <div class="divider"></div>

  <div class="company">
    <div><span class="company__label">P:</span> 02 9561 3048</div>
    <div>www.harcourtmemorials.com.au</div>
    <div>Suite 17, 8 Palfrey Lane, West Carlow,</div>
    <div>Sydney NSW 2156</div>
  </div>

  <div class="person person--secondary">
    <div class="person__name">Lewis Harcourt</div>
    <div class="person__role">Director</div>
    <div class="contact-line">
      <span>0491630572</span>
      <svg class="icon" viewBox="0 0 10 10"><path d="M2 0.5 L3.6 2.6 L2.8 3.6 Q4 6 6.4 7.2 L7.4 6.4 L9.5 8 L8.3 9.5 Q2 8.5 0.5 1.7 Z"/></svg>
    </div>
    <div class="contact-line">
      <span>lewis@harcourtmemorials.com.au</span>
      <svg class="icon" viewBox="0 0 10 10"><path d="M0.5 2 H9.5 V8 H0.5 Z M1 2.5 L5 5.5 L9 2.5" stroke="#333438" stroke-width="0.8"/></svg>
    </div>
  </div>
</section>

<section class="card card--back">
  <div class="brand-name">Harcourt Memorials</div>
</section>

</body>
</html>
```